I need a business card designed using the logo provided either vertical or horizontal......Harbourline Property Group is an Australian based real estate company that caters for the upper end of the market so the design of the business card "must reflect" the companies image!!
Colour combinations are optional but "must be realistic" and must be able to be accurately useable CMYK colours.
Please consider that any colours used "must be able to be used" and be suitable in following designs for "pull out banner signs" and "real estate signs".
The colours and the font in the attached designs are for example and other combinations are encouraged.
Target Market(s)
The High End of the Australian real estate market
Industry/Entity Type
Business
Contact Information for Business Card
Logo - Business Name - Director + Licensed Real Estate Agent - Mobile Number (Cell Phone) - Business Number - Fax - Email Address - Web address
Requirements
Must have
- Designs and colours (CMYK) that can easily be interpreted by an Australian printer.
Nice to have
- Some alternative ideas on colour and font..........the ones provided are ok and have been provided as an example but I am looking for alternative ideas
Should not have
- Loud, overly bright colours. Designs that do not reflect the professional standards of the business.
- Designs that look good on a computer monitor but can not be re-created on a printing press.............this is most important when it comes to shading etc.

```html
<!DOCTYPE html>
<html lang="en">
<head>
<meta charset="utf-8">
<title>Harbourline Property Group – Business Card</title>
<link rel="stylesheet" href="https://fonts.googleapis.com/css2?family=Open+Sans:wght@400;600&display=swap">
<style>
  :root {
    --bg: #e4e4e4;
    --card: #f7f7f7;
    --maroon: #3a0d16;
    --maroon-light: #4a1320;
    --maroon-accent: #8a1e32;
    --ink: #4a4a4a;
    --ink-soft: #6b6b6b;
  }
  * { box-sizing: border-box; margin: 0; padding: 0; }
  html, body { width: 1200px; height: 1192px; overflow: hidden; }
  body {
    background: var(--bg);
    font-family: "Open Sans", Arial, sans-serif;
    position: relative;
  }
  .card {
    position: absolute;
    top: 446px;
    width: 520px;
    height: 300px;
    background: var(--card);
    overflow: hidden;
    box-shadow: 0 6px 18px rgba(0,0,0,0.12);
  }
  .card--contact { left: 60px; }
  .card--brand { left: 620px; }

  .contact { position: absolute; left: 36px; top: 30px; }
  .contact__name {
    font-size: 15px; letter-spacing: 4px; text-transform: uppercase;
    color: var(--ink); font-weight: 400;
  }
  .contact__role {
    margin-top: 4px; font-size: 9px; letter-spacing: 2px; text-transform: uppercase;
    color: var(--maroon-accent); font-weight: 600;
  }
  .contact__company {
    margin-top: 10px; font-size: 9px; letter-spacing: 2px; text-transform: uppercase;
    color: var(--maroon-accent); font-weight: 600;
  }
  .contact__list { list-style: none; margin-top: 6px; }
  .contact__item {
    display: flex; align-items: center; gap: 8px;
    font-size: 11.5px; color: var(--ink-soft); line-height: 18px;
  }
  .contact__icon { width: 12px; height: 12px; flex: none; }

  .wordmark {
    position: absolute; color: var(--maroon-accent);
    font-weight: 600; text-transform: uppercase; letter-spacing: 2px;
    display: flex; align-items: center; gap: 8px; white-space: nowrap;
  }
  .wordmark__dot { width: 10px; height: 10px; border-radius: 50%; background: var(--maroon-accent); }
  .card--contact .wordmark { right: 28px; top: 198px; font-size: 12px; }
  .card--brand .wordmark { left: 50%; top: 72px; transform: translateX(-50%); font-size: 15px; }

  .contact-band {
    position: absolute; left: 0; right: 0; bottom: 0; height: 64px;
    background: linear-gradient(180deg, var(--maroon-light) 0%, var(--maroon) 100%);
  }
  .skyline-band {
    position: absolute; left: 0; right: 0; bottom: 0; height: 150px;
    background: linear-gradient(180deg, var(--maroon-light) 0%, var(--maroon) 100%);
  }
</style>
</head>
<body>

  <section class="card card--contact" aria-label="Business card front">
    <div class="contact">
      <h1 class="contact__name">Daniel Hartley</h1>
      <p class="contact__role">CEO</p>
      <p class="contact__company">Harbourline Property Group</p>
      <ul class="contact__list">
        <li class="contact__item">
          <svg class="contact__icon" viewBox="0 0 12 12"><path d="M6 11s4-4 4-6.5a4 4 0 0 0-8 0C2 7 6 11 6 11z" fill="var(--maroon-accent)"/><circle cx="6" cy="4.5" r="1.4" fill="var(--card)"/></svg>
          18 Wharf Terrace, Kirribilli, Sydney.
        </li>
        <li class="contact__item">
          <svg class="contact__icon" viewBox="0 0 12 12"><rect x="3" y="1" width="6" height="10" rx="1" fill="none" stroke="var(--maroon-accent)" stroke-width="1.2"/><circle cx="6" cy="9" r="0.7" fill="var(--maroon-accent)"/></svg>
          +61 412 555 019
        </li>
        <li class="contact__item">
          <svg class="contact__icon" viewBox="0 0 12 12"><path d="M3 1h2l1 3-1.5 1a6 6 0 0 0 2.5 2.5L8 6l3 1v2a1 1 0 0 1-1 1A9 9 0 0 1 2 2a1 1 0 0 1 1-1z" fill="var(--maroon-accent)"/></svg>
          +61 2 5550 1842
        </li>
        <li class="contact__item">
          <svg class="contact__icon" viewBox="0 0 12 12"><rect x="1" y="2.5" width="10" height="7" fill="none" stroke="var(--maroon-accent)" stroke-width="1.2"/><path d="M1 2.5l5 4 5-4" fill="none" stroke="var(--maroon-accent)" stroke-width="1.2"/></svg>
          daniel@harbourlinepg.com
        </li>
        <li class="contact__item">
          <svg class="contact__icon" viewBox="0 0 12 12"><circle cx="6" cy="6" r="4.8" fill="none" stroke="var(--maroon-accent)" stroke-width="1.2"/><path d="M1.2 6h9.6M6 1.2c-2.5 3-2.5 6.6 0 9.6M6 1.2c2.5 3 2.5 6.6 0 9.6" fill="none" stroke="var(--maroon-accent)" stroke-width="1"/></svg>
          www.harbourlinepg.com
        </li>
      </ul>
    </div>

    <div class="wordmark"><span class="wordmark__dot"></span>Harbourline Property Group</div>

    <div class="contact-band" role="img" aria-label="Decorative maroon band with gold and silver accent along the lower card"></div>
  </section>

  <section class="card card--brand" aria-label="Business card back">
    <div class="wordmark"><span class="wordmark__dot"></span>Harbourline Property Group</div>
    <div class="skyline-band" role="img" aria-label="City skyline silhouette in deep maroon across the lower card"></div>
  </section>

</body>
</html>
```